elegant beautiful Hang tag for a novelty makeup towel

It's a black hand towel in the shape of a little black dress. it is called PETAL CHARM TOWEL, it is a CLEAN SLATE MAKEUP TOWEL. (doesn't show our makeup stains) Made in USA

Target Market(s)

ALL Women , Makeup artists, novelty THIS WILL BE IN THE HALVERGATE STORES AND KESTRELMOOR STORES.

Industry/Entity Type

Makeup

Contact Information for Business Card

I actually need a hang tag for a homemade handmade towel. I have a logo that I want on the tag and know what we want to say on it, on back needs to say "The essential to every girl's wardrobe. So when the little black dress comes off, our PETAL CHARM TOWEL is there to help you wash your day away. Include website www.petalcharmtowel.com OH INCLUDE TM (trademark sign next to logo please. Also, in small print on back from the makers of THE ORIGINAL CLEAN SLATE MAKEUP TOWEL. handmade in USA. also CLEAN SLATE MAKEUP TOWEL IN big font on front under logo sign with light colored pink lips after 'CLEAN SLATE" but have no idea about fonts, graphics, placement or design. Want it classy, elegant, girly! COLORS LIGHT BEIGER BACKGROUND WITH BLACK WRITING/ DESIGNS

Font styles to use
Serif
Decorative
Script

Colors
fff3d1

Requirements
Must have
• Black cream girly , also state in big writing that it's a " clean slate makeup towel" with a tiny light pink lip between the show and makeup. Include www.petalcharmtowel.com Brightwater Fenn, LLC
Nice to have
• Perhaps an outline of a little black dress. A black scroll edge of some sort around card. Classy

```html
<!DOCTYPE html>
<html lang="en">
<head>
<meta charset="utf-8">
<title>Petal Charm Towel – Hang Tag</title>
<link rel="stylesheet" href="https://fonts.googleapis.com/css2?family=Montserrat:wght@400;500;600&display=swap">
<style>
  :root {
    --page-bg: #2b2b2b;
    --cream: #fff3d1;
    --card-black: #050505;
    --petal-pink: #f0838f;
    --soft-pink: #f6b8bf;
    --ink: #1a1a1a;
    --rule-grey: #8a8a8a;
  }
  * { box-sizing: border-box; margin: 0; padding: 0; }
  html, body {
    width: 1200px; height: 900px; overflow: hidden;
    background: var(--page-bg);
    font-family: "Montserrat", Arial, sans-serif;
  }
  .stage { position: relative; width: 1200px; height: 900px; }

  .tag {
    position: absolute;
    width: 700px; height: 400px;
    border-radius: 24px;
    overflow: hidden;
    box-shadow: 0 14px 30px rgba(0,0,0,0.45);
  }

  /* Front of tag */
  .tag--front {
    left: 90px; top: 70px;
    background: var(--cream);
    display: flex; flex-direction: column; align-items: center; justify-content: center;
    gap: 26px;
  }
  .brand-mark {
    display: flex; align-items: center; gap: 14px;
    color: var(--ink);
    font-weight: 600; font-size: 28px; letter-spacing: 4px;
  }
  .brand-mark__dot {
    width: 20px; height: 20px; border-radius: 50%;
    background: var(--ink);
  }
  .tm { font-size: 12px; letter-spacing: 0; align-self: flex-start; margin-left: -10px; }
  .front-claim {
    display: flex; align-items: center; gap: 12px;
    color: var(--ink);
    font-size: 24px; font-weight: 500; letter-spacing: 2px;
  }
  .front-claim__accent {
    width: 16px; height: 9px; border-radius: 50%;
    background: var(--soft-pink);
  }
  .front-web {
    font-size: 20px; font-weight: 500; color: var(--ink); letter-spacing: 0.3px;
  }

  /* Back of tag */
  .tag--back {
    left: 410px; top: 430px;
    background: var(--card-black);
  }
  .back-shapes { position: absolute; inset: 0; }
  .back-logo {
    position: absolute; left: 34px; top: 66px;
    width: 290px; text-align: center;
  }
  .back-logo__name {
    color: var(--cream);
    font-weight: 400; font-size: 18px; letter-spacing: 3px;
    white-space: nowrap;
    padding-bottom: 8px;
    border-bottom: 1px solid var(--rule-grey);
  }
  .back-logo__name sup { font-size: 9px; letter-spacing: 0; }
  .back-logo__tag {
    margin-top: 7px;
    color: var(--petal-pink);
    font-size: 10px; font-weight: 500; letter-spacing: 1.5px;
  }

  .tag-copy {
    position: absolute; right: 30px; top: 48px;
    width: 215px;
    text-align: right; color: var(--ink);
  }
  .tag-copy__lead {
    color: var(--petal-pink);
    font-size: 15px; font-weight: 600; line-height: 1.3;
    margin-bottom: 10px;
  }
  .tag-copy__body { font-size: 12.5px; line-height: 1.5; margin-bottom: 14px; }
  .tag-copy__web {
    display: flex; justify-content: flex-end; align-items: center; gap: 8px;
    font-size: 13px; font-weight: 500; margin-bottom: 14px;
  }
  .tag-copy__icon { width: 12px; height: 12px; flex: none; }
  .tag-copy__fine { font-size: 9.5px; line-height: 1.5; letter-spacing: 0.3px; }
</style>
</head>
<body>
<main class="stage">

  <section class="tag tag--front" aria-label="Tag front">
    <div class="brand-mark">
      <span class="brand-mark__dot"></span>
      <span>PETAL CHARM TOWEL</span>
      <span class="tm">™</span>
    </div>
    <p class="front-claim">
      <span>CLEAN SLATE</span>
      <span class="front-claim__accent"></span>
      <span>MAKEUP TOWEL</span>
    </p>
    <p class="front-web">www.petalcharmtowel.com</p>
  </section>

  <section class="tag tag--back" aria-label="Tag back">
    <svg class="back-shapes" viewBox="0 0 700 400" width="700" height="400" aria-hidden="true">
      <path d="M402 0 C 290 95, 285 300, 420 400 L 700 400 L 700 0 Z" fill="var(--petal-pink)"/>
      <path d="M432 0 C 332 90, 318 290, 448 400 L 700 400 L 700 0 Z" fill="var(--cream)"/>
    </svg>

    <div class="back-logo">
      <p class="back-logo__name">PETAL CHARM TOWEL<sup>™</sup></p>
      <p class="back-logo__tag">CLEAN SLATE MAKEUP TOWEL</p>
    </div>

    <div class="tag-copy">
      <p class="tag-copy__lead">The essential to every girl's wardrobe.</p>
      <p class="tag-copy__body">So when the little black dress comes off, our PETAL CHARM TOWEL is there to help you wash your day away.</p>
      <p class="tag-copy__web">www.petalcharmtowel.com
        <svg class="tag-copy__icon" viewBox="0 0 12 12" aria-hidden="true"><circle cx="6" cy="6" r="5" fill="var(--petal-pink)"/><path d="M1 6 H11 M6 1 C3.5 3.5 3.5 8.5 6 11 M6 1 C8.5 3.5 8.5 8.5 6 11" fill="none" stroke="var(--cream)" stroke-width="0.8"/></svg>
      </p>
      <p class="tag-copy__fine">From the makers of THE ORIGINAL CLEAN SLATE MAKEUP TOWEL</p>
      <p class="tag-copy__fine">Handmade in USA · Brightwater Fenn, LLC</p>
    </div>
  </section>

</main>
</body>
</html>
```